Australian Trucking Company Requires Professional Looking Stationary

We require a professional looking stationary design that incorporates our newly designed logo.

Our business, called "Brell Haulage Contracting", provides contracting work, transport and logistics to business in Western Australia particularly with links to the mining sector.

We are a small business looking to expand and our new logo and our new stationary will help develop our brand image in our market place.

Target Market(s)

Businesses and Corporation with links to the Mining Sector

Industry/Entity Type

Small Business

Requirements
Must have
• The letterhead must have the following details:
The new logo

Text saying: "Brell Holdings Pty Ltd (ACN 582 316 907) ATF The Brell Discretionary Trust T/AS"
"ABN 71 834 209 553"
Address "P.O Box 817 Wattlegrove WA, 6958"
Phone: 08 9352 7140
Email: brellhaul@mailbox-example.com.au

The text on the letterhead should be editable as the details are likely to change in the near future. Provision should be made for a website address all though one isn't available at the moment.

The styling, layout and font text is entirely up to the designer.

```html
<!DOCTYPE html>
<html lang="en">
<head>
<meta charset="utf-8">
<title>Brell Haulage Contracting – Business Cards</title>
<link rel="stylesheet" href="https://fonts.googleapis.com/css2?family=Arimo:wght@400;700&display=swap">
<style>
  :root {
    --page: #e8e3dc;
    --red-deep: #6e0006;
    --red: #b3121b;
    --red-text: #8e0f14;
    --swoosh: #a9a9ab;
    --white: #ffffff;
    --ink: #3b3b3b;
    --slate-light: #6b6b6b;
    --slate-dark: #333333;
  }
  * { margin: 0; padding: 0; box-sizing: border-box; }
  html, body { width: 1200px; height: 1200px; overflow: hidden; }
  body {
    background: var(--page);
    font-family: "Arimo", Arial, sans-serif;
    position: relative;
  }
  .card {
    position: absolute;
    width: 838px;
    height: 478px;
    overflow: hidden;
    box-shadow: 0 4px 14px rgba(0,0,0,.25);
  }
  .card-front { left: 86px; top: 80px; background: var(--white); }
  .card-back {
    left: 284px; top: 650px; width: 840px; height: 480px;
    background: radial-gradient(circle at 35% 40%, var(--slate-light), var(--slate-dark) 80%);
  }
  .card-art { position: absolute; inset: 0; }
  .brand {
    position: absolute;
    font-weight: 700;
    text-transform: uppercase;
    line-height: 1;
  }
  .brand span { display: block; }
  .front-brand { left: 218px; top: 52px; font-size: 48px; color: var(--red-text); }
  .front-brand span + span { margin-top: 6px; }
  .brand-square { position: absolute; }
  .front-square { left: 40px; top: 62px; width: 120px; height: 120px; background: var(--ink); }
  .address { position: absolute; left: 21px; top: 228px; font-size: 19px; color: var(--ink); }
  .person-name { position: absolute; left: 21px; top: 286px; font-size: 31px; font-weight: 700; color: var(--red-text); }
  .person-title { position: absolute; left: 21px; top: 330px; font-size: 23px; letter-spacing: 2px; color: var(--red-text); }
  .contact-list {
    position: absolute; right: 20px; top: 365px;
    list-style: none; color: var(--white); font-size: 18px;
  }
  .contact-list li { display: flex; align-items: center; gap: 8px; height: 32px; }
  .contact-list svg { width: 16px; height: 16px; flex: none; }
  .web-address {
    position: absolute; right: 46px; top: 40px;
    color: var(--white); font-size: 28px; letter-spacing: 2px;
  }
  .web-address b { font-weight: 700; letter-spacing: 3px; }
  .back-square { left: 60px; top: 150px; width: 180px; height: 180px; background: var(--white); }
  .back-brand { left: 306px; top: 168px; font-size: 56px; color: var(--white); }
  .back-brand span + span { margin-top: 8px; }
  .legal {
    position: absolute; left: 306px; top: 354px;
    color: var(--white); font-size: 20px; line-height: 37px;
  }
</style>
</head>
<body>

<section class="card card-front">
  <svg class="card-art" viewBox="0 0 838 478" preserveAspectRatio="none" aria-hidden="true">
    <defs>
      <radialGradient id="redField" cx="0.6" cy="0.85" r="0.8">
        <stop offset="0" stop-color="var(--red)"/>
        <stop offset="1" stop-color="var(--red-deep)"/>
      </radialGradient>
    </defs>
    <rect width="838" height="478" fill="url(#redField)"/>
    <path d="M0 0 L540 0 C700 10 735 95 705 175 C640 330 370 440 0 478 Z" fill="var(--swoosh)"/>
    <path d="M0 0 L525 0 C680 12 712 95 684 170 C620 320 360 432 0 472 Z" fill="var(--white)"/>
  </svg>
  <div class="brand-square front-square"></div>
  <h1 class="brand front-brand"><span>Brell</span><span>Haulage</span><span>Contracting</span></h1>
  <p class="address">P.O Box 817, Wattlegrove WA, 6958</p>
  <p class="person-name">Your Name</p>
  <p class="person-title">Title</p>
  <ul class="contact-list">
    <li>
      <svg viewBox="0 0 16 16"><circle cx="8" cy="8" r="7" fill="none" stroke="currentColor" stroke-width="1.4"/><path d="M5.5 4.5 L7 4.5 L7.5 6.5 L6.6 7.2 C7 8.2 7.8 9 8.8 9.4 L9.5 8.5 L11.5 9 L11.5 10.5 C8 11 5 8 5.5 4.5Z" fill="currentColor"/></svg>
      08 9352 7140
    </li>
    <li>
      <svg viewBox="0 0 16 16"><rect x="1" y="4" width="14" height="9" fill="currentColor"/><path d="M1 4 L8 9 L15 4" fill="none" stroke="#8a0b10" stroke-width="1.2"/></svg>
      brellhaul@mailbox-example.com.au
    </li>
    <li>
      <svg viewBox="0 0 16 16" fill="none" stroke="currentColor" stroke-width="1.1"><circle cx="8" cy="8" r="7"/><ellipse cx="8" cy="8" rx="3" ry="7"/><path d="M1 8 H15 M2.5 4.5 H13.5 M2.5 11.5 H13.5"/></svg>
      www.brellhaul-example.com
    </li>
  </ul>
</section>

<section class="card card-back">
  <p class="web-address">www.<b>brellhaul-example</b>.com</p>
  <div class="brand-square back-square"></div>
  <h2 class="brand back-brand"><span>Brell</span><span>Haulage</span><span>Contracting</span></h2>
  <p class="legal">Brell Holdings Pty Ltd<br>(ACN 582 316 907)<br>ATF The Brell Discretionary Trust T/AS</p>
</section>

</body>
</html>
```